Bandbanner für Melodic Metal Band
Zielgruppe
Velvet Harbor ist eine Melodic Metal Band.
Wir brauchen ein neues Design für Backdrops (Bandbanner) die wir in verschiedenen Grössen drucken könnten.
(Bisher hatten wir die Grössen 500 cm x 300 cm, 400 cm x 250 cm und 200 cm x 200 cm)
Unser Bandlogo soll modern und inspiriert rüberkommen, um unsere Musik und Show zusätzlich zu unterstreichen.
Aufgabenstellung
- das Bandlogo soll stylisch und cool präsentiert sein (z.B. mit zusätzlichen Elementen ergänzt, umspielt, umrahmt... )
- einzigartig, Blickfang, auf uns zugeschnitten
- Das Design soll neu und neutral sein. Also nicht direkt bezogen auf eines unserer Alben. Wir möchten es für verschiedene Zwecke und für längere Zeit benutzen können
- modern, cool, vielleicht frech, kann Farben enthalten, hell/dunkel, mystisch
- soll zu unserem ganzen Auftreten und Style passen
- unsere Musik und Inhalte sind melodiös, modern, mal hart, mal sanfter, mal etwas dunkler, anklagend oder nachdenklich aber immer mit einer Prise Helligkeit und Hoffnung, nicht destruktiv. Deshalb nicht zu morbide oder zu klischeehaft, aber es darf gerne mysteriös oder melancholisch oder auch schlicht und speziell sein
(Das Logo und Sign könnten wir übrigens als AI, CDR, EPS, JPG, PDF, PNG und PSD zur Verfügung stellen).

```html
<!DOCTYPE html>
<html lang="de">
<head>
<meta charset="utf-8">
<title>Velvet Harbor – Bandbanner</title>
<link href="https://fonts.googleapis.com/css2?family=Open+Sans:wght@400;700&display=swap" rel="stylesheet">
<style>
  :root {
    --page: #fbfbfb;
    --night: #130f0e;
    --smoke: #2a9ea0;
    --smoke-deep: #1b5d63;
    --ink-light: #f2f2f2;
    --logo-steel: #c9e3ea;
  }
  * { margin: 0; padding: 0; box-sizing: border-box; }
  html, body {
    width: 1200px;
    height: 1200px;
    overflow: hidden;
    background: var(--page);
    font-family: "Open Sans", Arial, sans-serif;
  }
  .banner {
    position: absolute;
    left: 14px;
    top: 270px;
    width: 1171px;
    height: 658px;
    background: var(--night);
    overflow: hidden;
  }
  .banner__smoke {
    position: absolute;
    inset: 0;
    background:
      radial-gradient(ellipse 220px 260px at 80px 420px, rgba(42,158,160,0.55), transparent 70%),
      radial-gradient(ellipse 260px 200px at 1000px 520px, rgba(42,158,160,0.45), transparent 70%),
      radial-gradient(ellipse 200px 140px at 720px 110px, rgba(42,158,160,0.40), transparent 70%),
      radial-gradient(ellipse 130px 170px at 1040px 120px, rgba(42,158,160,0.45), transparent 70%),
      radial-gradient(ellipse 320px 160px at 560px 330px, rgba(27,93,99,0.45), transparent 75%),
      radial-gradient(ellipse 240px 180px at 240px 600px, rgba(27,93,99,0.5), transparent 75%),
      var(--night);
  }
  .members {
    position: absolute;
    top: 44px;
    left: 0;
    width: 100%;
    height: 18px;
    list-style: none;
  }
  .members__name {
    position: absolute;
    transform: translateX(-50%);
    font-size: 12.5px;
    letter-spacing: 0.4px;
    color: var(--ink-light);
    white-space: nowrap;
  }
  .band-name {
    position: absolute;
    left: 0;
    top: 278px;
    width: 100%;
    text-align: center;
    font-weight: 700;
    font-size: 100px;
    line-height: 120px;
    letter-spacing: 4px;
    color: var(--logo-steel);
    text-transform: uppercase;
  }
  .tagline {
    position: absolute;
    left: 396px;
    top: 540px;
    width: 400px;
    text-align: center;
    font-size: 11.8px;
    line-height: 15.6px;
    letter-spacing: 0.3px;
    color: var(--ink-light);
  }
</style>
</head>
<body>
  <section class="banner">
    <div class="banner__smoke" role="img" aria-label="Türkisfarbener Rauch auf dunklem Hintergrund"></div>

    <ul class="members">
      <li class="members__name" style="left:209px">SABINE KRAUSEL</li>
      <li class="members__name" style="left:447px">MARCO VALENDRI</li>
      <li class="members__name" style="left:711px">JONAS PFERL</li>
      <li class="members__name" style="left:950px">LUKAS AMSTEIN</li>
    </ul>

    <h1 class="band-name">Velvet Harbor</h1>

    <p class="tagline">
      Lorem ipsum dolor sit amet, consectetur adipiscing elit,<br>
      sed do eiusmod tempor incididunt ut labore et dolore<br>
      magna aliqua. Quis ipsum suspendisse ultrices gravida. sis.
    </p>
  </section>
</body>
</html>
```